Coastline Premier Retreats Business Card Design

Design a business card for Coastline Premier Retreats. Look at the website for colors and reference. Card should have logo, name, title, office number, mobile number, email, URL and a tagline like, "Luxury Hotel & Resort Email Marketing" (This might change).

https://www.coastlinepremierretreats.example

The rest I will leave up to your imagination.

Contact Information for Business Card

Logo, name, title, office number, mobile number, email, URL and a tagline like, "Luxury Hotel & Resort Email Marketing" (This might change).

```html
<!DOCTYPE html>
<html lang="en">
<head>
<meta charset="utf-8">
<title>Coastline Premier Retreats – Business Card</title>
<link rel="stylesheet" href="https://fonts.googleapis.com/css2?family=Arimo:wght@400;700&display=swap">
<style>
  :root {
    --orange: #f47b20;
    --ink: #111111;
    --paper: #ffffff;
    --stage: #e9e7e4;
    --sky: #6f9fd0;
    --sea: #1f9a9a;
    --forest: #3f6b34;
    --stone: #8a8f7d;
  }
  * { box-sizing: border-box; margin: 0; padding: 0; }
  html, body {
    width: 1200px; height: 900px; overflow: hidden;
    background: var(--stage);
    font-family: "Arimo", Arial, sans-serif;
  }
  .stage {
    width: 1200px; height: 900px;
    display: flex; flex-direction: column; align-items: center; justify-content: center;
    gap: 40px;
  }
  .card {
    position: relative; width: 700px; height: 400px;
    overflow: hidden; background: var(--paper);
    box-shadow: 0 6px 18px rgba(0,0,0,.18);
  }
  /* Front */
  .card-front__scene {
    position: absolute; inset: 0;
    background:
      linear-gradient(180deg, var(--sky) 0%, #8fb7d8 18%, transparent 34%),
      linear-gradient(100deg, var(--forest) 0%, #5b7f3c 30%, var(--sea) 52%, #2aa5a3 72%, var(--forest) 92%);
  }
  .card-front__scene::after {
    content: ""; position: absolute; inset: 0;
    background: linear-gradient(180deg, transparent 60%, rgba(40,60,35,.55) 100%);
  }
  .card-front__name {
    position: absolute; left: 0; right: 0; top: 170px;
    text-align: center; color: var(--paper);
    font-weight: 700; font-size: 40px; letter-spacing: 1px; text-transform: uppercase;
  }
  /* Back */
  .brand-name {
    position: absolute; left: 50px; top: 170px; width: 280px;
    color: var(--ink); font-weight: 700; font-size: 26px; line-height: 1.15;
    text-transform: uppercase; letter-spacing: .5px;
  }
  .divider {
    position: absolute; left: 350px; top: 70px; width: 2px; height: 175px;
    background: var(--orange);
  }
  .details { position: absolute; left: 372px; top: 52px; color: var(--ink); }
  .details__name {
    color: var(--orange); font-weight: 700; font-size: 24px;
    text-transform: uppercase; margin-bottom: 6px;
  }
  .details__role { font-size: 16px; line-height: 20px; }
  .contacts { list-style: none; margin-top: 12px; }
  .contacts li {
    display: flex; align-items: center; gap: 8px;
    font-size: 14px; line-height: 20px;
  }
  .contacts svg { width: 14px; height: 14px; flex: none; }
  .wave { position: absolute; inset: 0; }
</style>
</head>
<body>
<main class="stage">
  <section class="card card-front">
    <div class="card-front__scene" role="img" aria-label="Coastal photograph of a rocky wooded headland above turquoise sea under a blue sky"></div>
    <p class="card-front__name">Coastline Premier Retreats</p>
  </section>

  <section class="card card-back">
    <svg class="wave" viewBox="0 0 700 400" aria-hidden="true">
      <path d="M0 362 C260 362 440 282 700 262 V400 H0 Z" fill="var(--orange)"/>
      <path d="M0 378 C270 378 460 296 700 280" fill="none" stroke="var(--paper)" stroke-width="5"/>
      <path d="M0 338 C230 346 420 282 680 262 C440 292 260 356 0 356 Z" fill="var(--ink)"/>
      <path d="M330 330 C420 300 520 272 680 258" fill="none" stroke="var(--orange)" stroke-width="1.5"/>
    </svg>

    <p class="brand-name">Coastline Premier Retreats</p>
    <div class="divider"></div>

    <div class="details">
      <h1 class="details__name">Daniel Marlowe</h1>
      <p class="details__role">Co-Founder</p>
      <p class="details__role">Luxury Hotel &amp; Resort</p>
      <p class="details__role">Email Marketing</p>
      <ul class="contacts">
        <li>
          <svg viewBox="0 0 16 16"><path d="M3 2h3l1.5 3.5-2 1.3a8 8 0 0 0 3.7 3.7l1.3-2L14 10v3a1 1 0 0 1-1 1A11 11 0 0 1 2 3a1 1 0 0 1 1-1z" fill="var(--orange)"/></svg>
          555-014-2789
        </li>
        <li>
          <svg viewBox="0 0 16 16"><rect x="4" y="1" width="8" height="14" rx="1.5" fill="none" stroke="var(--orange)" stroke-width="1.6"/><circle cx="8" cy="12.5" r=".9" fill="var(--orange)"/></svg>
          555-019-7087
        </li>
        <li>
          <svg viewBox="0 0 16 16"><rect x="1" y="3" width="14" height="10" fill="var(--orange)"/><path d="M1 3l7 6 7-6" fill="none" stroke="var(--paper)" stroke-width="1.3"/></svg>
          info@coastlinepremierretreats.example
        </li>
        <li>
          <svg viewBox="0 0 16 16"><circle cx="8" cy="8" r="7" fill="var(--orange)"/><path d="M1 8h14M8 1c-3 3-3 11 0 14M8 1c3 3 3 11 0 14" fill="none" stroke="var(--paper)" stroke-width="1"/></svg>
          www.coastlinepremierretreats.example
        </li>
      </ul>
    </div>
  </section>
</main>
</body>
</html>
```